Trading Company needs a business card design, letter head design and email signature

We need a double-sided business card design, letter head design and an email signature. We have a logo design.

Possible Tag Lines:
• “Connecting Worlds, Building Excellence.”
• “Global Sourcing, Local Excellence.”
• “Bridging Borders, Building Quality.”
• “Worldwide Partnerships, Superior Goods.”
• “Where Quality Meets Affordability”

Services Offered:
Procurement
Fabrication
Distribution
Logistics
Import/Export

Requirements
Must have
• Nice quality double sided Business Card design, Letterhead design needs to be A4
Nice to have
• possible ideas on tag lines

```html
<!DOCTYPE html>
<html lang="en">
<head>
<meta charset="utf-8">
<title>Kestrane – Stationery</title>
<link href="https://fonts.googleapis.com/css2?family=Open+Sans:wght@400;600;700;800&family=Great+Vibes&display=swap" rel="stylesheet">
<style>
  :root {
    --brand-red: #e8262b;
    --card-red: #eb282b;
    --card-red-deep: #d61f24;
    --ink: #1d1d1f;
    --charcoal: #161616;
    --paper: #ffffff;
    --backdrop: #e2e2e2;
  }
  * { box-sizing: border-box; margin: 0; padding: 0; }
  html, body { width: 1200px; height: 933px; overflow: hidden; }
  body {
    background: var(--backdrop);
    font-family: "Open Sans", sans-serif;
    color: var(--ink);
    position: relative;
  }

  /* ---------- Letterhead ---------- */
  .letterhead {
    position: absolute; left: 98px; top: 53px;
    width: 550px; height: 777px;
    background: var(--paper);
  }
  .letterhead .brand {
    position: absolute; left: 27px; top: 128px;
    display: flex; align-items: center; gap: 8px;
  }
  .brand-mark { width: 14px; height: 14px; background: var(--brand-red); display: block; }
  .brand-name {
    font-weight: 800; font-size: 26px; letter-spacing: 1.5px;
    color: var(--brand-red); line-height: 1; white-space: nowrap;
  }
  .letterhead .contact {
    position: absolute; left: 387px; top: 30px;
    border-left: 1.5px solid var(--brand-red);
    padding-left: 18px; height: 64px;
    font-size: 10.5px; line-height: 12.3px; color: #333;
  }
  .contact-line { display: flex; align-items: center; gap: 4px; white-space: nowrap; }
  .contact-line svg { width: 8px; height: 8px; flex: none; }
  .contact .address { margin-top: 7px; }

  .letter-body {
    position: absolute; left: 27px; top: 177px; width: 495px;
    font-size: 11.1px; line-height: 12.1px;
  }
  .letter-body .date { font-size: 12px; }
  .letter-body .recipient { margin-top: 13px; font-size: 11.5px; line-height: 13px; }
  .letter-body .company { margin-top: 13px; font-size: 11.5px; line-height: 13px; }
  .letter-body .salutation { margin-top: 15px; font-size: 14px; font-weight: 600; }
  .letter-body p.copy { text-align: justify; margin-top: 12px; }
  .letter-body p.copy:first-of-type { margin-top: 14px; }
  .letter-body .closing { margin-top: 32px; font-size: 11.5px; }
  .letter-body .signature {
    margin-top: 68px; font-family: "Great Vibes", cursive;
    font-size: 27px; line-height: 1; color: #111;
  }

  /* ---------- Business card, front ---------- */
  .card {
    position: absolute; left: 757px; width: 343px; height: 195px;
    border-radius: 22px; overflow: hidden;
  }
  .card-front { top: 379px; background: var(--charcoal); color: #fff; }
  .card-front .brand {
    position: absolute; left: 22px; top: 118px;
    display: flex; align-items: center; gap: 7px;
  }
  .card-front .brand-name { font-size: 23px; }
  .card-front .divider {
    position: absolute; left: 197px; top: 49px; width: 1.2px; height: 74px;
    background: var(--brand-red);
  }
  .card-front .holder { position: absolute; left: 211px; top: 46px; width: 122px; }
  .holder-name { color: var(--brand-red); font-weight: 600; font-size: 14.5px; line-height: 16px; white-space: nowrap; }
  .holder-role { font-size: 10px; line-height: 12px; }
  .holder .contact-line { font-size: 10px; line-height: 12.3px; }
  .holder .lines { margin-top: 6px; }
  .holder .address { margin-top: 7px; font-size: 10px; line-height: 12.3px; }
  .taglines { position: absolute; list-style: none; font-size: 6.6px; line-height: 9.6px; white-space: nowrap; }
  .taglines li::before { content: "• "; }
  .taglines.left { left: 13px; top: 155px; }
  .taglines.right { left: 191px; top: 163px; }

  /* ---------- Business card, back ---------- */
  .card-back { top: 601px; background: var(--card-red); color: #fff; text-align: center; }
  .card-back .brand-name {
    position: absolute; left: 0; right: 0; top: 100px;
    font-size: 31px; letter-spacing: 2px; color: var(--card-red-deep);
  }
  .services-title {
    position: absolute; left: 0; right: 0; top: 150px;
    font-size: 8px; font-weight: 700; letter-spacing: .2px;
  }
  .services {
    position: absolute; left: 0; right: 0; top: 166px;
    display: flex; justify-content: center; gap: 8px;
    list-style: none; font-size: 10px; white-space: nowrap;
  }
</style>
</head>
<body>

<svg width="0" height="0" style="position:absolute">
  <defs>
    <symbol id="icon-phone" viewBox="0 0 10 10">
      <path d="M1 3.5C1 2 2.5 1.5 5 1.5S9 2 9 3.5L7.5 4 7 3H3L2.5 4ZM2.5 5h5l1 3.5h-7Z" fill="#e8262b"/>
    </symbol>
    <symbol id="icon-mail" viewBox="0 0 10 10">
      <rect x="1" y="2.5" width="8" height="6" fill="none" stroke="#e8262b" stroke-width="1.2"/>
      <path d="M1 2.5 5 6l4-3.5" fill="none" stroke="#e8262b" stroke-width="1.1"/>
    </symbol>
    <symbol id="icon-globe" viewBox="0 0 10 10">
      <circle cx="5" cy="5" r="4" fill="#e8262b"/>
      <path d="M1 5h8M5 1c-2 2.5-2 5.5 0 8M5 1c2 2.5 2 5.5 0 8" fill="none" stroke="#fff" stroke-width=".7"/>
    </symbol>
  </defs>
</svg>

<!-- Letterhead -->
<section class="letterhead">
  <div class="brand">
    <span class="brand-mark"></span>
    <span class="brand-name">KESTRANE</span>
  </div>

  <div class="contact">
    <div class="contact-line"><svg><use href="#icon-phone"/></svg>020 5550 1846</div>
    <div class="contact-line"><svg><use href="#icon-mail"/></svg>hello@kestrane.com</div>
    <div class="contact-line"><svg><use href="#icon-globe"/></svg>www.kestrane.com</div>
    <div class="address">Your address, City<br>State, Zip 1234</div>
  </div>

  <div class="letter-body">
    <div class="date">January-03-2020</div>
    <div class="recipient">Mr, Paul Mercer<br>President</div>
    <div class="company">Halden Group<br>123 Street Name, Suite# 10<br>City, State, 120023</div>
    <div class="salutation">Dear Mr, Paul</div>
    <p class="copy">Lorem ipsum dolor sit amet, consectetur adipiscing elit, sed do eiusmod tempor incididunt ut labore et dolore magna aliqua. Ut enim ad minim veniam, quis nostrud exercitation ullamco laboris nisi ut aliquip ex ea commodo consequat. Duis aute irure dolor in reprehenderit in voluptate velit esse cillum dolore eu fugiat nulla pariatur.</p>
    <p class="copy">Lorem ipsum dolor sit amet, consectetur adipiscing elit, sed do eiusmod tempor incididunt ut labore et dolore magna aliqua. Ut enim ad minim veniam, quis nostrud exercitation ullamco laboris nisi ut aliquip ex ea commodo consequat. Duis aute irure dolor in reprehenderit in voluptate velit esse cillum dolore eu fugiat nulla pariatur.</p>
    <p class="copy">Lorem ipsum dolor sit amet, consectetur adipiscing elit, sed do eiusmod tempor incididunt ut labore et dolore magna aliqua. Ut enim ad minim veniam, quis nostrud exercitation ullamco laboris nisi ut aliquip ex ea commodo consequat.</p>
    <p class="copy">Excepteur sint occaecat cupidatat non proident, sunt in culpa qui officia deserunt mollit anim id est laborum. re et dolore magnam aliquam quaerat voluptatem.</p>
    <div class="closing">Regards</div>
    <div class="signature">Lena Arkwright</div>
  </div>
</section>

<!-- Business card front -->
<section class="card card-front">
  <div class="brand">
    <span class="brand-mark"></span>
    <span class="brand-name">KESTRANE</span>
  </div>
  <div class="divider"></div>
  <div class="holder">
    <div class="holder-name">OWEN HARTLEY</div>
    <div class="holder-role">Managing Director</div>
    <div class="lines">
      <div class="contact-line"><svg><use href="#icon-phone"/></svg>020 5550 1847</div>
      <div class="contact-line"><svg><use href="#icon-mail"/></svg>owen@kestrane.com</div>
      <div class="contact-line"><svg><use href="#icon-globe"/></svg>www.kestrane.com</div>
    </div>
    <div class="address">Your address, City<br>State, Zip 1234</div>
  </div>
  <ul class="taglines left">
    <li>“Connecting Worlds, Building Excellence.”</li>
    <li>“Global Sourcing, Local Excellence.”</li>
    <li>“Bridging Borders, Building Quality.”</li>
  </ul>
  <ul class="taglines right">
    <li>“Worldwide Partnerships, Superior Goods.”</li>
    <li>“Where Quality Meets Affordability”</li>
  </ul>
</section>

<!-- Business card back -->
<section class="card card-back">
  <span class="brand-name">KESTRANE</span>
  <div class="services-title">SERVICES OFFERED</div>
  <ul class="services">
    <li>Procurement</li>
    <li>Fabrication</li>
    <li>Distribution</li>
    <li>Logistics Import/Export</li>
  </ul>
</section>

</body>
</html>
```